Redesign of a Reputation Management Website

StandingMender.com Requirement Doc
Reference Site: NameTidy.com (should NOT copy this site but be patterned in a similar way because we are changing the back end and functionality similar to it)
StandingMender.com is a functional active site that needs a redesign.
FRONT END
Landing / Home Page:
• Should be built with WordPress for ease of use
• Should contain high quality imagery
• Should contain logo
• Should contain Navigation links on top right or top center
1. Personal
2. Business
3. About us
4. Account Login
5. Sign Up
• Should be broken into sections
1. Header – High Quality Image/Slider/Social Media Icons/Contact Info
2. Information
3. Services Personal / Business
4. Sign Up
5. Footer – Links/Contacts/ Social media
6. Sub footer- Info Links
Landing / Home Page Colours:
Main colours should be contrasting light and dark blues like #1A9BFC, #31A5FC and #60BAF7, with minimal green like #77AE00 as an accent colour. The footer and sub footer should be #1C3344
Landing / Home Functional Requirements:
All front end links should link out their individual pages and/or back end processes, this includes navigation menu items, footer links, and sign up and social media buttons. All linked pages should contain I quality information, Graphics, calls to action and sign up options.
Sign up should have two options, Sign up with social media accounts or standard sign up form.
Login should have two options, Login with social media accounts or standard login form.
Target Market(s)
People that are looking to manage their reputation or repair it, or manage their brand, monitor their reputation online
Industry/Entity Type
Management
Number of Pages Required
1 page
Look and feel
Each slider illustrates characteristics of the customer's brand and the style your logo design should communicate.

```html
<!DOCTYPE html>
<html lang="en">
<head>
<meta charset="utf-8">
<title>Standing Mender – Control and protect your online reputation</title>
<link rel="stylesheet" href="https://fonts.googleapis.com/css2?family=Montserrat:wght@400;500;600;700&family=Open+Sans:wght@400;600&display=swap">
<style>
:root{
  --blue-strong:#1A9BFC;
  --blue-mid:#31A5FC;
  --blue-light:#60BAF7;
  --green:#77AE00;
  --navy:#1C3344;
  --navy-deep:#172b3a;
  --ink:#1d1d1d;
  --grey:#555;
  --white:#fff;
}
*{margin:0;padding:0;box-sizing:border-box}
html,body{width:1200px;height:2320px;overflow:hidden;background:#fff}
body{font-family:"Montserrat",sans-serif;color:var(--ink);position:relative}
.section{position:absolute;left:0;width:1200px}

/* header */
.site-header{top:0;height:96px;background:linear-gradient(180deg,var(--blue-mid),var(--blue-strong))}
.brand{position:absolute;left:100px;top:22px;display:flex;align-items:center;gap:12px;color:var(--white)}
.brand-mark{width:40px;height:40px;background:var(--white);border-radius:50%;opacity:.9}
.brand-name{font-size:30px;font-weight:700;line-height:1}
.brand-tag{font-size:13px;font-weight:600;margin-top:6px;display:block}
.main-nav{position:absolute;left:657px;top:33px;display:flex;align-items:center;font-size:14px;color:var(--white)}
.main-nav a{color:inherit;text-decoration:none;margin-right:30px}
.main-nav .nav-signup{border:2px solid var(--white);padding:8px 14px;margin:0}

/* hero */
.hero{top:96px;height:458px;background:linear-gradient(90deg,#f4f4f4 0%,#e9e9e9 60%,#dcdcdc 100%);border-bottom:2px solid #ccc}
.hero-photo{position:absolute;right:90px;top:0;width:520px;height:456px;background:radial-gradient(ellipse at 55% 45%,#d8dde3 0%,#c9ced4 40%,rgba(220,220,220,0) 72%)}
.hero-copy{position:absolute;left:167px;top:48px}
.hero-title{font-size:40px;font-weight:400;color:var(--blue-strong);line-height:1.1}
.hero-sub{font-size:20px;color:#555;margin-top:14px;line-height:1.3}
.hero-sub strong{color:#333;font-weight:600}
.hero-lead{font-size:20px;color:#333;margin-top:20px}
.social-row{display:flex;align-items:center;gap:14px;margin-top:16px}
.social-btn{width:60px;height:60px;display:flex;flex-direction:column;align-items:center;justify-content:flex-end;padding-bottom:6px;color:var(--white);font-size:9px;font-weight:600}
.social-btn svg{margin-bottom:6px}
.social-btn.flink{background:#145ba8}
.social-btn.chirp{background:var(--blue-strong)}
.social-btn.mail{background:var(--green)}
.social-dot{width:20px;height:20px;border-radius:50%;background:var(--white);margin-bottom:8px}
.or{font-size:13px;color:#666}
.call-btn{margin-top:20px;width:350px;height:46px;background:var(--blue-light);color:var(--white);font-size:22px;display:flex;align-items:center;justify-content:center;gap:12px}
.slide-arrow{position:absolute;top:155px}

/* welcome */
.welcome{top:554px;height:199px;text-align:center}
.welcome h1{font-size:27px;font-weight:600;color:var(--blue-strong);margin-top:28px}
.welcome p{font-size:13px;font-weight:500;line-height:26px;width:720px;margin:14px auto 0}
.btn-green{display:inline-block;background:var(--green);color:var(--white);font-size:16px;font-weight:500;padding:11px 12px;margin-top:14px}

/* services */
.services-band{top:753px;height:57px;background:var(--blue-strong);text-align:center;color:var(--white);font-size:26px;font-weight:500;line-height:57px}
.services-band::before{content:"";position:absolute;left:588px;top:-1px;border:12px solid transparent;border-top-color:#fff}
.service-row{height:230px}
.service-row.personal{top:810px}
.service-row.business{top:1040px;height:225px}
.service-text{position:absolute;width:520px}
.service-text h2{font-size:15px;font-weight:500;color:#222}
.service-text p{font-family:"Open Sans",sans-serif;font-size:13px;line-height:25px;margin-top:14px;text-align:justify;color:#222}
.service-photo{position:absolute;top:0;width:600px;height:100%}
.personal .service-photo{left:600px;background:linear-gradient(135deg,#9fd0f5,#5fb0ee 55%,#4da3e6);border-left:2px solid #8cc3ef}
.business .service-photo{left:0;background:linear-gradient(135deg,#8fba3a,#6e9d1e 55%,#557f12)}
.personal .service-text{left:52px;top:34px}
.business .service-text{left:638px;top:42px}

/* signup */
.signup{top:1265px;height:545px;background:linear-gradient(120deg,#3f83b5 0%,#4d93c3 45%,#3a7db1 100%)}
.signup-photo{position:absolute;left:0;top:0;width:1200px;height:545px;background:radial-gradient(ellipse at 38% 55%,rgba(150,205,240,.45),rgba(70,140,190,0) 60%)}
.signup h2{position:absolute;left:652px;top:45px;font-size:24px;font-weight:500;color:var(--white)}
.signup-panel{position:absolute;left:652px;top:93px;width:322px;height:402px;background:rgba(40,70,95,.55);padding:30px 16px 0}
.field{height:38px;border:1.5px solid rgba(255,255,255,.8);margin-bottom:14px;color:var(--white);font-size:11px;font-weight:600;line-height:35px;padding-left:16px}
.btn-signup{display:inline-block;background:var(--green);color:var(--white);font-size:17px;font-weight:500;height:46px;line-height:46px;padding:0 12px}
.signup-note{font-family:"Open Sans",sans-serif;font-style:italic;color:var(--white);font-size:10px;line-height:12px;margin-top:10px;width:270px}
.social-signup{position:absolute;left:135px;top:370px}
.social-signup h3{font-size:24px;font-weight:500;color:var(--white)}
.social-signup .social-row{margin-top:18px}
.social-signup .or{color:#dfeaf3}

/* partners */
.partners{top:1810px;height:102px;background:#fff}
.partner-badge{position:absolute;top:26px;width:180px;height:50px;background:#e3e3e3;border-radius:6px}

/* footer */
.site-footer{top:1912px;height:338px;background:var(--navy);color:var(--white)}
.footer-col{position:absolute;top:34px}
.footer-col h4{font-size:18px;font-weight:500;margin-bottom:20px}
.footer-col li{list-style:none;font-family:"Open Sans",sans-serif;font-size:12px;line-height:25.5px}
.contact-line{display:flex;gap:14px;font-family:"Open Sans",sans-serif;font-size:12px;line-height:20px;margin-bottom:8px}
.contact-line svg{flex:none;margin-top:3px}
.sub-footer{top:2250px;height:70px;background:var(--navy-deep);color:#cdd6dd;font-size:10px}
.sub-footer p{position:absolute;left:845px;top:30px}
</style>
</head>
<body>

<header class="section site-header">
  <div class="brand">
    <span class="brand-mark"></span>
    <div><span class="brand-name">Standing Mender</span><span class="brand-tag">Reputation Consulting Since 1992</span></div>
  </div>
  <nav class="main-nav">
    <a href="#">Personal</a><a href="#">Business</a><a href="#">About us</a><a href="#">Account Login</a><a href="#" class="nav-signup">Sign Up</a>
  </nav>
</header>

<section class="section hero">
  <div class="hero-photo" role="img" aria-label="Young man in glasses sitting and using a tablet"></div>
  <svg class="slide-arrow" style="left:98px" width="36" height="72" viewBox="0 0 36 72"><polyline points="34,2 2,36 34,70" fill="none" stroke="#1A9BFC" stroke-width="1.5"/></svg>
  <svg class="slide-arrow" style="left:1060px" width="36" height="72" viewBox="0 0 36 72"><polyline points="2,2 34,36 2,70" fill="none" stroke="#1A9BFC" stroke-width="1.5"/></svg>
  <div class="hero-copy">
    <h1 class="hero-title">Control and protect<br>Your Online Reputation</h1>
    <p class="hero-sub">Ranked one of the worlds leading <strong>Internet<br>Reputation management</strong></p>
    <p class="hero-lead">Sign up For FREE With</p>
    <div class="social-row">
      <a class="social-btn flink"><span class="social-dot"></span>FaceLink</a>
      <a class="social-btn chirp"><span class="social-dot"></span>Chirper</a>
      <span class="or">OR</span>
      <a class="social-btn mail"><svg width="26" height="20" viewBox="0 0 26 20"><rect x="1" y="1" width="24" height="18" rx="2" fill="none" stroke="#fff" stroke-width="2"/><polyline points="1,2 13,11 25,2" fill="none" stroke="#fff" stroke-width="2"/></svg>Email</a>
    </div>
    <div class="call-btn"><svg width="12" height="22" viewBox="0 0 12 22"><rect x="1" y="1" width="10" height="20" rx="2" fill="none" stroke="#fff" stroke-width="2"/><circle cx="6" cy="17" r="1.3" fill="#fff"/></svg>Call Us : +1 555 260 4418</div>
  </div>
</section>

<section class="section welcome">
  <h1>WELCOME TO OUR WEBSITE</h1>
  <p>Temporibus autem quibusdam et aut officiis debitis aut rerum necessitatibus saepe eveniet ut et voluptates repudiandae sint et molestiae non recusandae.</p>
  <a class="btn-green">GET STARTED</a>
</section>

<div class="section services-band">SERVICES</div>

<section class="section service-row personal">
  <div class="service-text">
    <h2>PERSONAL</h2>
    <p>Temporibus autem quibusdam et aut officiis debitis aut rerum necessitatibus saepe eveniet ut et voluptates repudiandae sint et molestiae non recusandae. Itaque earum rerum hic tenetur a sapiente delectus, ut aut reiciendis voluptatibus maiores alias consequatur aut perferendis doloribus asperiores repellat</p>
  </div>
  <div class="service-photo" role="img" aria-label="Couple looking together at a tablet, blue tinted"></div>
</section>

<section class="section service-row business">
  <div class="service-photo" role="img" aria-label="Two businessmen talking at a desk, green tinted"></div>
  <div class="service-text">
    <h2>BUSINESS</h2>
    <p>Temporibus autem quibusdam et aut officiis debitis aut rerum necessitatibus saepe eveniet ut et voluptates repudiandae sint et molestiae non recusandae. Itaque earum rerum hic tenetur a sapiente delectus, ut aut reiciendis voluptatibus maiores alias consequatur aut perferendis doloribus asperiores repellat</p>
  </div>
</section>

<section class="section signup">
  <div class="signup-photo" role="img" aria-label="Man in glasses working on a laptop with glowing interface icons, blue tinted"></div>
  <h2>SIGNUP FORM</h2>
  <form class="signup-panel">
    <div class="field">FIRST NAME</div>
    <div class="field">LAST NAME</div>
    <div class="field">USER NAME</div>
    <div class="field">PASSWORD</div>
    <div class="field">CONFIRM PASSWORD</div>
    <a class="btn-signup">SIGNUP NOW</a>
    <p class="signup-note">Sed ut perspiciatis unde omnis iste natus error sit voluptatem accusantium doloremque laudantium, totam rem aperiam.</p>
  </form>
  <div class="social-signup">
    <h3>SOCILA SIGNUP</h3>
    <div class="social-row">
      <a class="social-btn flink"><span class="social-dot"></span>FaceLink</a>
      <a class="social-btn chirp"><span class="social-dot"></span>Chirper</a>
      <span class="or">OR</span>
      <a class="social-btn mail"><svg width="26" height="20" viewBox="0 0 26 20"><rect x="1" y="1" width="24" height="18" rx="2" fill="none" stroke="#fff" stroke-width="2"/><polyline points="1,2 13,11 25,2" fill="none" stroke="#fff" stroke-width="2"/></svg>Email</a>
    </div>
  </div>
</section>

<section class="section partners">
  <svg style="position:absolute;left:128px;top:30px" width="24" height="44" viewBox="0 0 24 44"><polyline points="22,2 2,22 22,42" fill="none" stroke="#666" stroke-width="1.5"/></svg>
  <div class="partner-badge" style="left:188px"></div>
  <div class="partner-badge" style="left:412px"></div>
  <div class="partner-badge" style="left:620px"></div>
  <div class="partner-badge" style="left:836px"></div>
  <svg style="position:absolute;left:1064px;top:30px" width="24" height="44" viewBox="0 0 24 44"><polyline points="2,2 22,22 2,42" fill="none" stroke="#666" stroke-width="1.5"/></svg>
</section>

<footer class="section site-footer">
  <div class="footer-col" style="left:142px">
    <h4>RESOURCES</h4>
    <ul><li>Case Studies</li><li>Free Reputation Check</li><li>Reputation Advice</li><li>Videos</li></ul>
  </div>
  <div class="footer-col" style="left:357px">
    <h4>SERVICES</h4>
    <ul><li>Personal Reputation</li><li>Business Reputation</li><li>Cheater Submission Removal</li><li>People Search Site Removal</li><li>Reputation Monitoring</li><li>Record Expungement</li><li>Mugshot Removal</li><li>Search Engine Name Removal</li><li>Online Review Management</li><li>Online Privacy Management</li></ul>
  </div>
  <div class="footer-col" style="left:623px">
    <h4>ABOUT</h4>
    <ul><li>Become A Partner</li><li>Company</li><li>FAQ'S</li><li>Our Team</li><li>Privacy Policy</li><li>TOS</li></ul>
  </div>
  <div class="footer-col" style="left:838px;width:240px">
    <h4>CONTACT INFO</h4>
    <div class="contact-line"><svg width="12" height="16" viewBox="0 0 12 16"><path d="M6 1a5 5 0 0 0-5 5c0 4 5 9 5 9s5-5 5-9a5 5 0 0 0-5-5z" fill="#fff"/><circle cx="6" cy="6" r="2" fill="#1C3344"/></svg><span>412-8800 Alder Road, Suite 210, Maple Grove, Ontario, Canada K0X 2B9</span></div>
    <div class="contact-line"><svg width="14" height="14" viewBox="0 0 14 14"><path d="M3 1l3 3-2 2c1 2 2 3 4 4l2-2 3 3-2 2C6 13 1 8 1 3z" fill="#fff"/></svg><span>+1 555 260 4418</span></div>
    <div class="contact-line" style="margin-top:18px"><svg width="16" height="12" viewBox="0 0 16 12"><rect x="1" y="1" width="14" height="10" fill="none" stroke="#fff" stroke-width="1.5"/><polyline points="1,1 8,7 15,1" fill="none" stroke="#fff" stroke-width="1.5"/></svg><span>hello@standingmender.com</span></div>
    <div class="contact-line" style="padding-left:30px;margin-top:12px"><span>www.StandingMender.com</span></div>
  </div>
</footer>

<div class="section sub-footer"><p>© 2015 • www.standingmender.com • Privacy policy</p></div>

</body>
</html>
```